BRIGHTHOLD PROPERTY MANAGEMENT INC. WEBSITE

Please make the website more family-friendly.

I want a website to help me build my property management business by adding listing properties and creating an online application. Im open to any other ideas.
I want a WordPress designer to code it.

Here is my current website. www.brighthold.biz

IDEA: I like the website design https://www.pelicanclimateservices.com/

Thank you

Tom

Number of Pages Required

5+ page

```html
<!DOCTYPE html>
<html lang="en">
<head>
<meta charset="utf-8">
<title>Brighthold Property Management</title>
<link href="https://fonts.googleapis.com/css2?family=Lora:wght@400;500;700&family=Inter:wght@400;600;700&display=swap" rel="stylesheet">
<style>
:root{
  --red:#a50f12;
  --pink:#f4e4e5;
  --grey:#f1f0f0;
  --ink:#2a2a2a;
  --black:#0b0b0b;
  --white:#fff;
}
*{box-sizing:border-box;margin:0;padding:0}
html,body{width:1200px;height:5217px;overflow:hidden}
body{position:relative;font-family:"Lora",serif;color:var(--ink);background:var(--white)}
.abs{position:absolute}
.btn-red{background:var(--red);color:var(--white);font-family:"Lora",serif;display:flex;align-items:center;justify-content:center}

/* header */
.site-header{position:absolute;left:0;top:0;width:1200px;height:160px;background:var(--white);border-bottom:1px solid #e5e5e5}
.brand{position:absolute;left:130px;top:30px;width:160px;text-align:center;color:var(--red)}
.brand-name{font-size:22px;font-weight:500;letter-spacing:1px;display:block}
.brand-sub{font-size:7px;letter-spacing:.4px;display:block;margin-top:3px}
.brand-mark{display:block;width:30px;height:30px;border:2px solid var(--red);margin:0 auto 6px}
.phone{left:650px;top:40px;height:32px;display:flex;align-items:center;gap:10px;font-size:17px}
.phone-icon{width:32px;height:32px;background:var(--red);border-radius:3px;display:flex;align-items:center;justify-content:center}
.btn-outline{left:862px;top:38px;width:96px;height:38px;border:1.5px solid var(--red);color:var(--red);font-size:15px;display:flex;align-items:center;justify-content:center}
.btn-login{left:973px;top:36px;width:96px;height:40px;font-size:15px}
.nav{left:380px;top:105px;display:flex;gap:26px;font-size:15px;color:var(--ink)}
.nav .active{color:var(--red);text-decoration:underline;text-underline-offset:4px}

/* hero */
.hero{left:0;top:160px;width:1200px;height:602px;background:linear-gradient(100deg,#4a3e36 0%,#7a4a3a 35%,#8f7b6c 60%,#a89a8c 100%)}
.hero-tag{left:132px;top:270px;padding:0 12px;height:56px;background:var(--red);color:var(--white);font-size:46px;font-weight:500;letter-spacing:1px;display:flex;align-items:center}
.hero-title{left:132px;top:352px;width:430px;color:var(--white);font-size:31px;font-weight:700;line-height:42px;text-transform:uppercase}
.search{left:310px;top:535px;width:580px;height:56px;background:var(--white);display:flex;align-items:center;justify-content:space-between;padding:0 22px 0 26px;font-size:13px;color:#333}

/* calculator */
.calc{left:130px;top:648px;width:940px;height:420px;background:var(--white);box-shadow:0 6px 24px rgba(0,0,0,.12)}
.calc-side{left:535px;top:0;width:405px;height:420px;background:#f7eeee}
.calc-title{left:52px;top:38px;font-size:30px}
.calc-art{left:370px;top:28px;width:145px;height:85px;background:linear-gradient(135deg,#e7c9c9,#c9a07a)}
.field-label{font-size:12px;color:var(--ink)}
.field{width:205px;height:44px;border:1px solid #999;font-size:12px;padding:0 14px;display:flex;align-items:center;justify-content:space-between}
.calc-btn{left:52px;top:325px;width:426px;height:48px;font-size:18px}
.calc-row{left:57px;width:295px;height:32px;display:flex;align-items:center;font-size:13px;padding-left:22px}
.calc-row.shade{background:#f0d7d8}
.calc-row span:first-child{width:148px}

/* headings */
.sec-title{font-size:30px;font-weight:400}
.rule{height:2px;width:100px;background:var(--red)}

/* listings */
.card{top:1272px;width:302px;height:504px;background:var(--white);border:1px solid #e6e6e6;box-shadow:0 2px 8px rgba(0,0,0,.08)}
.card-img{left:0;top:0;width:100%;height:225px;background:linear-gradient(180deg,#7ea7d6 0%,#a9c3de 45%,#8a7b64 75%,#6b7a4c 100%)}
.card-title{left:30px;top:252px;width:250px;font-size:15px;line-height:24px}
.card-price{left:30px;font-size:22px;color:var(--red)}
.card-addr{left:30px;font-size:11px}
.specs{left:30px;display:flex;font-size:10px;line-height:13px}
.specs div{padding:0 14px 0 0;margin-right:14px;border-right:1px solid #444}
.specs div:last-child{border:none}
.card-btn{left:30px;width:103px;height:30px;font-size:12px}

/* welcome */
.welcome-img{left:0;top:1855px;width:585px;height:485px;background:linear-gradient(135deg,#5b4e43 0%,#a9998a 40%,#e9e4dc 70%,#c8b9a8 100%)}
.welcome{left:585px;top:1855px;width:615px;height:485px;background:var(--grey)}
.body-copy{font-size:14.5px;line-height:24px;color:#333}
.btn-small{height:36px;font-size:13px;padding:0 22px}

/* pm */
.pm-img{left:585px;top:2340px;width:615px;height:540px;background:linear-gradient(135deg,#2b1f3f 0%,#6e5488 50%,#3a2d52 100%)}
.areas{left:130px;top:2935px;width:940px;display:grid;grid-template-columns:210px 250px 235px 245px;font-size:12px;line-height:21px}
.areas li{list-style:none;padding-left:16px;position:relative}
.areas li::before{content:"";position:absolute;left:0;top:7px;border-left:6px solid var(--red);border-top:4px solid transparent;border-bottom:4px solid transparent}

/* services */
.services{left:0;top:3130px;width:1200px;height:592px;background:linear-gradient(180deg,#8b7ab8 0%,#b88fb8 35%,#d7a8b8 50%,#3b3e4b 70%,#2a2c30 100%)}
.svc{position:absolute;width:140px;text-align:center;color:var(--white);font-size:13px;line-height:20px}
.svc-ring{position:absolute;width:92px;height:92px;border-radius:50%;border:3px solid var(--white);display:flex;align-items:center;justify-content:center}
.svc-stem{position:absolute;width:2px;background:rgba(255,255,255,.85)}
.services-title{left:0;top:3480px;width:1200px;text-align:center;color:var(--white);font-size:50px}

/* rates */
.rate-row{left:115px;width:345px;height:48px;display:flex;align-items:center;padding-left:18px;font-size:15px}
.rate-row.shade{background:var(--pink)}
.rate-row span:first-child{width:195px}
.rates-img{left:462px;top:3780px;width:608px;height:430px;background:linear-gradient(135deg,#8d7660 0%,#c9b59c 50%,#5e4c3c 100%)}

/* contact */
.contact{left:0;top:4270px;width:1200px;height:575px;background:linear-gradient(120deg,#7fb54a 0%,#c9a63a 30%,#b8d86a 45%,#d8e7b0 62%,#e4ecd5 100%)}
.input{left:690px;width:378px;height:40px;background:var(--white);border-radius:6px;font-size:11px;padding:12px 18px}
.submit{left:690px;top:4725px;width:378px;height:57px;border-radius:6px;font-size:22px}

/* footer */
.footer{left:0;top:4845px;width:1200px;height:372px;background:var(--black);color:var(--white);font-family:"Inter",sans-serif}
.foot-brand{left:130px;top:70px;width:265px;text-align:center;color:var(--red);font-family:"Lora",serif}
.foot-brand .brand-name{font-size:33px;letter-spacing:2px}
.foot-brand .brand-sub{font-size:11px;letter-spacing:.8px}
.foot-head{font-size:13px;font-weight:700;letter-spacing:.3px}
.foot-head::after{content:"";display:block;width:100px;height:1px;background:#777;margin-top:8px}
.foot-item{display:flex;gap:12px;align-items:flex-start;font-size:11px;line-height:14px}
.dot{width:22px;height:22px;border-radius:50%;background:var(--white);flex:none;display:flex;align-items:center;justify-content:center}
.foot-menu{font-size:11px;line-height:19.5px}
.copyright{left:0;top:5180px;width:1200px;text-align:center;font-size:11px;color:#fff;font-family:"Inter",sans-serif}
</style>
</head>
<body>

<header class="site-header">
  <div class="brand"><span class="brand-mark"></span><span class="brand-name">BRIGHTHOLD</span><span class="brand-sub">PROPERTY MANAGEMENT &amp; SERVICES</span></div>
  <div class="abs phone"><span class="phone-icon"><svg width="16" height="16" viewBox="0 0 24 24"><path fill="#fff" d="M6.6 10.8a15 15 0 0 0 6.6 6.6l2.2-2.2c.3-.3.7-.4 1-.2 1.1.4 2.3.6 3.6.6.6 0 1 .4 1 1V20c0 .6-.4 1-1 1A17 17 0 0 1 3 4c0-.6.4-1 1-1h3.5c.6 0 1 .4 1 1 0 1.3.2 2.5.6 3.6.1.3 0 .7-.2 1z"/></svg></span>(555) 014-2870</div>
  <div class="abs btn-outline">Contact</div>
  <div class="abs btn-red btn-login">Login</div>
  <nav class="abs nav"><span class="active">Home</span><span>Listings</span><span>Owners</span><span>Prospect Tenants</span><span>About</span><span>Community</span><span>Mortgage Info</span></nav>
</header>

<section class="abs hero" role="img" aria-label="Family standing in front of a brick two-storey house"></section>
<div class="abs hero-tag">CALL TODAY</div>
<h1 class="abs hero-title">Get 1 Month Property Management Fee Off.<br>$120 Value!!</h1>
<div class="abs search"><span>Enter Address, City, Zip, Neighbourhood or #MLS</span><svg width="22" height="22" viewBox="0 0 24 24"><circle cx="10" cy="10" r="7" fill="none" stroke="#a50f12" stroke-width="2.4"/><path d="M15 15l6 6" stroke="#a50f12" stroke-width="2.4"/></svg></div>

<section class="abs calc">
  <div class="abs calc-side"></div>
  <h2 class="abs calc-title" style="font-weight:400">Mortgage Calculator</h2>
  <div class="abs calc-art" role="img" aria-label="Small house balanced on a seesaw against a dollar sign"></div>
  <div class="abs field-label" style="left:52px;top:132px">Loan amount</div>
  <div class="abs field-label" style="left:272px;top:132px">Loan length</div>
  <div class="abs field" style="left:52px;top:157px">$150000</div>
  <div class="abs field" style="left:272px;top:157px">30 Years</div>
  <div class="abs field-label" style="left:52px;top:226px">Annual interest</div>
  <div class="abs field-label" style="left:272px;top:226px">Pay periodicity</div>
  <div class="abs field" style="left:52px;top:252px">3.7%</div>
  <div class="abs field" style="left:272px;top:252px">Annually<svg width="12" height="8"><path d="M0 0h12L6 7z" fill="#222"/></svg></div>
  <div class="abs btn-red calc-btn">Calculate</div>
  <div style="position:absolute;left:535px;top:28px">
    <div class="abs calc-row" style="top:0"><span>Loan amount:</span><span>$150,000.00</span></div>
    <div class="abs calc-row shade" style="top:44px"><span>Loan length:</span><span>30 years</span></div>
    <div class="abs calc-row" style="top:88px"><span>Annual interest:</span><span>3.70%</span></div>
    <div class="abs calc-row shade" style="top:132px"><span>Pay periodicity:</span><span>Annually</span></div>
    <div class="abs calc-row" style="top:176px"><span>Annually payment:</span><span>$8,361.34</span></div>
    <div class="abs calc-row shade" style="top:220px"><span>Total paid:</span><span>$250,840.15</span></div>
    <div class="abs calc-row" style="top:264px"><span>Total interest:</span><span>$100,840.15</span></div>
    <div class="abs calc-row shade" style="top:308px"><span>Total periods:</span><span>30</span></div>
  </div>
</section>

<h2 class="abs sec-title" style="left:0;top:1155px;width:1200px;text-align:center">Listings</h2>
<div class="abs rule" style="left:550px;top:1220px"></div>

<article class="abs card" style="left:130px">
  <div class="abs card-img" role="img" aria-label="Single-storey rental house with a large tree"></div>
  <div class="abs card-title">Fantastic opportunity<br>2 Bdrm x 1 Bth ADU Unit!!</div>
  <div class="abs card-price" style="top:312px">$2,000.00</div>
  <div class="abs card-addr" style="top:346px">1730 Linden Ct, Oakland, CA 94610</div>
  <div class="abs specs" style="top:384px"><div>693<br>Sq. Ft</div><div>2<br>Bedrooms</div><div>1<br>Bathrooms</div></div>
  <div class="abs btn-red card-btn" style="top:440px">View Details</div>
</article>
<article class="abs card" style="left:450px">
  <div class="abs card-img" role="img" aria-label="Single-storey apartment building front"></div>
  <div class="abs card-title">5210 Maple Row #3</div>
  <div class="abs card-price" style="top:290px">$2,000.00</div>
  <div class="abs card-addr" style="top:324px">Carmichael, CA 95608, Sacramento, US</div>
  <div class="abs specs" style="top:384px"><div>693<br>Sq. Ft</div><div>2<br>Bedrooms</div><div>1<br>Bathrooms</div></div>
  <div class="abs btn-red card-btn" style="top:440px">View Details</div>
</article>
<article class="abs card" style="left:768px">
  <div class="abs card-img" role="img" aria-label="Single-storey rental house with a large tree"></div>
  <div class="abs card-title">Nice &amp; Clean 3 bd. x 1 bth.<br>Apartment.</div>
  <div class="abs card-price" style="top:312px">$1695.00</div>
  <div class="abs card-addr" style="top:346px">Sacramento, CA 95818, Sacramento, US</div>
  <div class="abs specs" style="top:384px"><div>693<br>Sq. Ft</div><div>2<br>Bedrooms</div><div>1<br>Bathrooms</div></div>
  <div class="abs btn-red card-btn" style="top:440px">View Details</div>
</article>

<div class="abs welcome-img" role="img" aria-label="Agents reviewing a tablet beside a small model house"></div>
<section class="abs welcome">
  <h2 class="abs" style="left:65px;top:70px;font-size:28px;font-weight:400">Welcome to Brighthold</h2>
  <div class="abs rule" style="left:65px;top:123px;width:125px"></div>
  <p class="abs body-copy" style="left:65px;top:160px;width:375px">Our vision for Brighthold Property Management is to provide the best Property Management Services to the Sacramento and surrounding areas. I am focused on providing a more personalized service to you and your tenants. This means we are a one-stop-shop. You only deal with me, no middle guy, so no time is wasted.</p>
  <div class="abs btn-red btn-small" style="left:65px;top:370px">Read More</div>
</section>

<section class="abs" style="left:0;top:2340px;width:585px;height:540px">
  <h2 class="abs" style="left:128px;top:55px;width:400px;font-size:28px;font-weight:400;line-height:42px">Property Management Elk Grove, Sacramento &amp; Surrounding Areas</h2>
  <div class="abs rule" style="left:128px;top:203px;width:125px"></div>
  <p class="abs body-copy" style="left:130px;top:242px;width:420px">Having the right property manager means having an agent who is committed to helping you and making being a home provider hassle free. I believe clear communication, work ethic, time management, staying focused and knowledge goes a long way in my business.</p>
  <p class="abs body-copy" style="left:130px;top:392px;width:420px">This commitment level has helped us build a remarkable track record of delivering results and maintaining a long lasting business partnership with our clients.</p>
  <div class="abs btn-red btn-small" style="left:130px;top:492px">Read More</div>
</section>
<div class="abs pm-img" role="img" aria-label="Hand pressing a digital property management interface"></div>

<ul class="abs areas">
  <div><li>Sacramento</li><li>Antelope</li><li>Carmichael</li><li>Citrus Heights</li><li>El Dorado County</li><li>El Dorado Hills</li></div>
  <div><li>Elverta</li><li>Fair Oaks</li><li>Folsom</li><li>Foothill Farms</li><li>Florin Vicinity</li><li>Land Park / Curtis Park</li></div>
  <div><li>Elk Grove / Laguna</li><li>Mather</li><li>Natomas</li><li>North Highlands</li><li>Orangevale</li><li>Galt</li></div>
  <div><li>Rancho Cordova / Gold River</li><li>Rancho Cordova / Anatolia &amp; Vicinity</li><li>Rancho Murieta</li><li>Rio Linda</li><li>Rocklin</li><li>Rosemont / Mayhew Vicinity</li></div>
</ul>

<section class="abs services" role="img" aria-label="Modern two-storey house at dusk with lit garage doors"></section>
<div class="svc" style="left:113px;top:3222px">Rent<br>Collection</div>
<div class="svc" style="left:250px;top:3186px">Mortgage &amp;<br>Utility Payments</div>
<div class="svc" style="left:392px;top:3186px">Accounting<br>Services</div>
<div class="svc" style="left:531px;top:3180px">Security<br>Deposits</div>
<div class="svc" style="left:663px;top:3186px">Inspections<br>of Property</div>
<div class="svc" style="left:815px;top:3186px">Repair &amp;<br>Maintenance<br>Service</div>
<div class="svc" style="left:955px;top:3232px">Leasing</div>
<div class="svc-ring" style="left:146px;top:3268px"><svg width="40" height="40" viewBox="0 0 40 40" fill="none" stroke="#fff" stroke-width="2"><rect x="8" y="10" width="24" height="14" rx="2"/><circle cx="20" cy="17" r="3"/><path d="M6 30h28"/></svg></div>
<div class="svc-ring" style="left:276px;top:3240px"><svg width="40" height="40" viewBox="0 0 40 40" fill="none" stroke="#fff" stroke-width="2"><path d="M6 20L20 8l14 12M10 17v15h20V17"/><path d="M20 20v8"/></svg></div>
<div class="svc-ring" style="left:422px;top:3240px"><svg width="40" height="40" viewBox="0 0 40 40" fill="none" stroke="#fff" stroke-width="2"><rect x="10" y="6" width="20" height="28" rx="2"/><path d="M14 12h12M14 18h4M22 18h4M14 24h4M22 24h4"/></svg></div>
<div class="svc-ring" style="left:554px;top:3234px"><svg width="40" height="40" viewBox="0 0 40 40" fill="none" stroke="#fff" stroke-width="2"><rect x="8" y="10" width="24" height="20" rx="2"/><circle cx="20" cy="20" r="5"/></svg></div>
<div class="svc-ring" style="left:690px;top:3240px"><svg width="40" height="40" viewBox="0 0 40 40" fill="none" stroke="#fff" stroke-width="2"><path d="M6 20L20 8l14 12M10 17v15h12"/><circle cx="28" cy="26" r="5"/><path d="M32 30l4 4"/></svg></div>
<div class="svc-ring" style="left:838px;top:3262px"><svg width="40" height="40" viewBox="0 0 40 40" fill="none" stroke="#fff" stroke-width="2"><path d="M10 30L28 12M26 8l6 6M12 10l18 20M8 12l4-4"/></svg></div>
<div class="svc-ring" style="left:978px;top:3268px"><svg width="40" height="40" viewBox="0 0 40 40" fill="none" stroke="#fff" stroke-width="2"><path d="M6 20L20 8l14 12M10 17v15h20V17"/><circle cx="20" cy="23" r="4"/></svg></div>
<div class="svc-stem" style="left:191px;top:3360px;height:60px"></div>
<div class="svc-stem" style="left:321px;top:3332px;height:90px"></div>
<div class="svc-stem" style="left:467px;top:3332px;height:85px"></div>
<div class="svc-stem" style="left:599px;top:3326px;height:80px"></div>
<div class="svc-stem" style="left:735px;top:3332px;height:85px"></div>
<div class="svc-stem" style="left:883px;top:3354px;height:65px"></div>
<div class="svc-stem" style="left:1023px;top:3360px;height:60px"></div>
<h2 class="abs services-title" style="font-weight:400">Property Management</h2>

<h2 class="abs sec-title" style="left:115px;top:3835px">Mortgage Rates</h2>
<div class="abs rate-row" style="top:3930px"><span>30-Year FHA Rate</span><span>7.07%</span></div>
<div class="abs rate-row shade" style="top:3978px"><span>30-Year Fixed Rate</span><span>5.88%</span></div>
<div class="abs rate-row" style="top:4026px"><span>20-Year Fixed Rate</span><span>7.19%</span></div>
<div class="abs rate-row shade" style="top:4074px"><span>15-Year Fixed Rate</span><span>6.61%</span></div>
<div class="abs rates-img" role="img" aria-label="Tablet on a wooden desk beside a coffee cup and pen"></div>

<section class="abs contact" role="img" aria-label="Yellow model house with a red for-rent tag on a green background"></section>
<h2 class="abs" style="left:688px;top:4322px;font-size:38px;font-weight:400">Contact Us</h2>
<div class="abs rule" style="left:690px;top:4393px;width:125px"></div>
<div class="abs input" style="top:4440px">First Name</div>
<div class="abs input" style="top:4495px">Last Name</div>
<div class="abs input" style="top:4548px">Email id</div>
<div class="abs input" style="top:4603px;height:97px">Message</div>
<div class="abs btn-red submit">Submit</div>

<footer class="abs footer">
  <div class="abs foot-brand"><span class="brand-mark" style="width:50px;height:50px;margin-bottom:14px"></span><span class="brand-name">BRIGHTHOLD</span><span class="brand-sub">PROPERTY MANAGEMENT &amp; SERVICES</span></div>
  <div class="abs" style="left:462px;top:58px;width:220px">
    <div class="foot-head">CONTACT US</div>
    <div class="foot-item" style="margin-top:22px"><span class="dot"><svg width="10" height="12" viewBox="0 0 10 12"><path d="M5 0a4 4 0 0 1 4 4c0 3-4 8-4 8S1 7 1 4a4 4 0 0 1 4-4z" fill="#000"/></svg></span><span>418 Larkspur Way #12,<br>Sacramento , CA 95820</span></div>
    <div class="foot-item" style="margin-top:20px"><span class="dot"><svg width="11" height="11" viewBox="0 0 24 24"><path fill="#000" d="M6.6 10.8a15 15 0 0 0 6.6 6.6l2.2-2.2c.3-.3.7-.4 1-.2 1.1.4 2.3.6 3.6.6.6 0 1 .4 1 1V20c0 .6-.4 1-1 1A17 17 0 0 1 3 4c0-.6.4-1 1-1h3.5c.6 0 1 .4 1 1 0 1.3.2 2.5.6 3.6.1.3 0 .7-.2 1z"/></svg></span><span>Call Us<br>(555) 014-2870</span></div>
    <div class="foot-item" style="margin-top:20px"><span class="dot"><svg width="11" height="9" viewBox="0 0 12 9"><rect width="12" height="9" fill="#000"/><path d="M0 0l6 5 6-5" stroke="#fff" fill="none"/></svg></span><span>E-mail Us<br>info@brighthold.biz</span></div>
  </div>
  <div class="abs" style="left:748px;top:58px;width:160px">
    <div class="foot-head">MENU</div>
    <div class="foot-menu" style="margin-top:14px">Home<br>Listings<br>Owners<br>Prospect Tenants<br>About<br>Community<br>Mortgage Info</div>
  </div>
  <div class="abs" style="left:960px;top:58px;width:160px">
    <div class="foot-head">FOLLOW US</div>
    <div class="foot-item" style="margin-top:24px;align-items:center"><span class="dot"></span><span>Like us on<br>NEIGHBORLY</span></div>
    <div class="foot-item" style="margin-top:22px;align-items:center"><span class="dot"></span><span>Follow us on<br>PROCIRCLE</span></div>
    <div class="foot-item" style="margin-top:22px;align-items:center"><span class="dot"></span><span>Follow us on<br>SNAPWALL</span></div>
  </div>
  <div class="abs" style="left:75px;top:285px;width:1050px;height:1px;background:#444"></div>
</footer>
<div class="abs copyright">Copyright © 2024 All Rights Reserved</div>

</body>
</html>
```